Marwick Law Letterhead

We need a new letterhead design for a Law Firm. The address for the law firm is 1475 Calloway Street, Suite 210, Houston, Texas 77041. Phone Number: 832-361-9027; Fax Number: 832-614-7359. The logo is uploaded to the project.

```html
<!DOCTYPE html>
<html lang="en">
<head>
<meta charset="utf-8">
<title>Marwick Law Letterhead</title>
<link href="https://fonts.googleapis.com/css2?family=Montserrat:wght@400;500&family=Tinos:wght@400&display=swap" rel="stylesheet">
<style>
  :root {
    --navy: #2b3a67;
    --red: #e0312a;
    --text-grey: #8d8d8d;
    --dark-grey: #444;
    --backdrop: #d9dadd;
    --paper: #ffffff;
    --signature-tone: #e4e5ea;
  }
  html, body { margin: 0; padding: 0; }
  body {
    width: 1200px; height: 1200px; overflow: hidden;
    background: var(--backdrop);
    font-family: "Montserrat", Arial, sans-serif;
  }
  .letterhead {
    position: absolute; left: 175px; top: 0;
    width: 849px; height: 1200px;
    background: var(--paper);
  }
  .brand {
    position: absolute; left: 43px; top: 56px;
    display: flex; align-items: center; gap: 12px;
  }
  .brand-mark { width: 34px; height: 34px; background: var(--navy); }
  .brand-block { display: flex; flex-direction: column; }
  .brand-name {
    font-family: "Tinos", "Times New Roman", serif;
    font-size: 31px; color: var(--navy); line-height: 1;
  }
  .brand-tagline {
    font-family: "Tinos", "Times New Roman", serif;
    font-size: 6px; letter-spacing: 1px; color: var(--navy);
    text-transform: uppercase; margin-top: 6px;
  }
  .contact {
    position: absolute; left: 619px; top: 40px;
    font-family: "Tinos", "Times New Roman", serif;
    font-size: 13.5px; color: var(--navy); line-height: 17.5px;
  }
  .contact-row { display: flex; align-items: center; gap: 6px; }
  .contact-row svg { width: 11px; height: 11px; fill: var(--red); }
  .contact-address { margin-top: 3px; }
  .header-rule {
    position: absolute; left: 41px; top: 119px;
    width: 767px; height: 2px; background: var(--navy);
  }
  .recipient {
    position: absolute; left: 86px; top: 262px;
    font-size: 11.5px; color: var(--text-grey); line-height: 19px;
  }
  .recipient-label { font-size: 14px; letter-spacing: 2px; color: var(--dark-grey); margin-bottom: 4px; }
  .recipient-name { font-size: 14px; color: var(--red); margin-bottom: 3px; }
  .letter-date {
    position: absolute; right: 86px; top: 264px;
    font-size: 11.5px; color: var(--dark-grey);
  }
  .letter-body {
    position: absolute; left: 86px; top: 428px; width: 678px;
    font-size: 12.6px; line-height: 15.1px; color: var(--text-grey);
    text-align: justify;
  }
  .letter-body p { margin: 0 0 15px; }
  .signature-mark {
    position: absolute; left: 86px; top: 848px;
    width: 146px; height: 34px; background: var(--signature-tone); border-radius: 4px;
  }
  .signatory {
    position: absolute; left: 84px; top: 894px;
    font-size: 13.5px; color: var(--dark-grey);
  }
  .signatory-role { font-size: 11px; color: var(--text-grey); margin-top: 2px; }
</style>
</head>
<body>
  <div class="letterhead">
    <div class="brand">
      <div class="brand-mark"></div>
      <div class="brand-block">
        <div class="brand-name">Marwick Law</div>
        <div class="brand-tagline">Your trust is our daily commitment</div>
      </div>
    </div>

    <div class="contact">
      <div class="contact-row">
        <svg viewBox="0 0 24 24"><path d="M6.6 10.8a15.1 15.1 0 0 0 6.6 6.6l2.2-2.2c.3-.3.7-.4 1-.2 1.1.4 2.3.6 3.6.6.6 0 1 .4 1 1V20c0 .6-.4 1-1 1A17 17 0 0 1 3 4c0-.6.4-1 1-1h3.5c.6 0 1 .4 1 1 0 1.3.2 2.5.6 3.6.1.3 0 .7-.2 1z"/></svg>
        <span>832-361-9027</span>
      </div>
      <div class="contact-row">
        <svg viewBox="0 0 24 24"><path d="M6 2h10v5H6zM3 9h18v11H3zm4 3v2h4v-2zm6 0v2h4v-2zm-6 4v2h4v-2zm6 0v2h4v-2z"/></svg>
        <span>832-614-7359</span>
      </div>
      <div class="contact-address">1475 Calloway Street<br>Suite 210, Houston, Texas 77041</div>
    </div>

    <div class="header-rule"></div>

    <div class="recipient">
      <div class="recipient-label">TO</div>
      <div class="recipient-name">Daniel Orsway</div>
      <div>Human Resources</div>
      <div>Brightfield Systems Inc.</div>
      <div>2208-B Linden Row, Fairhaven</div>
      <div>F42 USA</div>
    </div>
    <div class="letter-date">Friday, 01/01/2018</div>

    <div class="letter-body">
      <p>Lorem ipsum dolor sit amet, consectetuer adipiscing elit, sed diam nonmmy nibh euismod tincidunt ut laoreet dolore magna aliquam erat volutpat. Ut wisi enim ad minim veniam, quis nostrud exerci tationmcorper suscipit lobortis nisl ut aliquip ex ea commodo consequat. Duis autem vel eum iriure dolor in hendrerit in vulputate velit esse molestie consequat, vel illum dolore eu feugiat nulla facilisis at vero eros et accumsan et iusto odio dignissim qui blandit praesent luptatum zzril delenit augue duis dolore te feugait nulla facilisi.</p>
      <p>Nam liber tempor cum soluta nobis eleifend option congue nihil imprdiet doming id quod mazim placerat facer possim assum. Typi non habent claritatem insitam;</p>
      <p>Est usus legentis in iis qui facit eorum claritatem.</p>
      <p>Investigationes demonstraverunt lectores legere me lius quod ii legunt saepius. Claritas est etiam processus dynamicus, qui sequitur mutationem consuetudium lectorum. Mirum est notare quam littera gothica, quam nunc putamus parum claram, anteposuerit litterarum formas humanitatis per seacula quarta decima et quinta decima. Eodem modo typi, qui nunc nobis videntur parum clari, fiant sollemnes in futurum.</p>
      <p>consectetuer adipiscing elit, sed diam nonummy nibh euismod tincidunt ut laoreet dolore magna aliquam erat volutpat. Ut wisi enim ad minim veniam, quis nostrud exerci tation ullamcorper suscipit lobortis nisl ut aliquip ex ea commodo consequat. Duis autem vel eum iriure dolor in hendrerit in vulputate velit esse molestie consequat, vel illum dolore eu feugiat nulla facilisis at vero eros et accumsan et iusto odio dignissim qui blandit praesent luptatum zzril delenit augue duis dolore te feugait nulla facilisi.</p>
      <p>Nam liber tempor cum soluta nobis eleifend option congue nihil imperdiet .</p>
    </div>

    <div class="signature-mark" role="img" aria-label="Handwritten signature of Peter Holloway"></div>
    <div class="signatory">
      <div>Peter Holloway</div>
      <div class="signatory-role">Managing Director</div>
    </div>
  </div>
</body>
</html>
```